Harlow Creek Church Invite Card

We are a vibrant multigenerational church outside of Raleigh, NC and are wanting a 'church invite card' that we can encourage our members to carry with them so that they can invite their friends to church.

These cards should have a modern feel (see http://brightmosaic.com/neat-card-ideas/ for the feel we are going for), match the branding of our website (www.harlowcreek.org) and include the following information on the back:

Service Times: Sunday @ 8:30 AM and 11:00 AM (Main Focus)
Website: www.harlowcreek.org (Main Focus)
Social Media: (You can simply use the icons for these if desired)
www.facebook.com/harlowcreekchurch
www.instagram.com/harlowcreekchurch
www.youtube.com/harlowcreekyouth
Address: 2847 Tamsin Parkway Wendell, NC 27594 (Not a main focus)
Phone: (919) 482-7093 (Not a main focus)

The front should simply say 'We look forward to meeting you!'

Logos: Attached you will find the necessary logos for this project.

Fonts and Colors: Here are the specific colors (See HCC_Website_Color_Palette.pdf) and fonts that are used on our website.
Pacifico
Helvetica
Open Sans Regular

Target Market(s)

Friends of our congregation

Industry/Entity Type

Church

Contact Information for Business Card

We will likely print through Lantern Printworks. The details of what they need can be found here: http://www.lanternprintworks.com/items/calling-card

Font styles to use
Other font styles liked:
• Pacifico, Helvetica, Open Sans Regular, Bebas Nue

Colors
0592cd
34a7d8
85cae6
cee9f5
0455a3
3176b5
85acd3
cfdfed

Requirements
Must have
• Sleek, eye catching design
Nice to have
• Rounded Corners, Our social media sites (CH, Snap and ClipHarbor)

```html
<!DOCTYPE html>
<html lang="en">
<head>
<meta charset="utf-8">
<title>Harlow Creek Church Invite Card</title>
<link rel="stylesheet" href="https://fonts.googleapis.com/css2?family=Open+Sans:wght@400;600;700&display=swap">
<style>
  :root {
    --blue: #0592cd;
    --blue-light: #34a7d8;
    --blue-deep: #0455a3;
    --ink: #141414;
    --paper: #ffffff;
    --backdrop: #e9edf1;
  }
  * { box-sizing: border-box; margin: 0; padding: 0; }
  html, body { width: 1200px; height: 780px; overflow: hidden; }
  body {
    background: var(--backdrop);
    font-family: "Open Sans", Helvetica, Arial, sans-serif;
    display: flex; align-items: center; justify-content: center; gap: 40px;
  }
  .card {
    position: relative; width: 540px; height: 309px; border-radius: 18px;
    overflow: hidden; box-shadow: 0 10px 28px rgba(0,0,0,.18);
  }
  .card-art { position: absolute; inset: 0; width: 100%; height: 100%; }

  /* Contact side */
  .card-front { background: var(--paper); }
  .front-website {
    position: absolute; right: -52px; top: 142px; width: 150px;
    transform: rotate(90deg); color: var(--paper);
    font-size: 12px; letter-spacing: .5px; text-align: center; white-space: nowrap;
  }
  .brand { position: absolute; display: flex; align-items: center; gap: 10px; color: var(--ink); font-weight: 700; white-space: nowrap; }
  .brand-dot { width: 22px; height: 22px; border-radius: 50%; background: var(--blue); flex: none; }
  .brand-name { line-height: 1; }
  .brand-name .line-main { display: block; font-size: 34px; letter-spacing: -.5px; }
  .brand-name .line-sub { display: block; font-size: 13px; letter-spacing: 3px; margin-top: 4px; }
  .card-front .brand { left: 36px; top: 44px; }

  .contact { position: absolute; left: 36px; top: 150px; color: var(--ink); font-size: 14px; line-height: 1.35; }
  .contact-phone { display: flex; align-items: center; gap: 8px; margin-top: 4px; }
  .phone-icon { width: 18px; height: 18px; border-radius: 3px; background: var(--blue-light); display: flex; align-items: center; justify-content: center; }
  .service-label { margin-top: 10px; color: var(--blue); font-size: 15px; }
  .service-times { font-size: 15px; }

  /* Logo side */
  .card-back { background: radial-gradient(ellipse at 55% 35%, var(--blue-light) 0%, var(--blue) 45%, var(--blue-deep) 100%); }
  .card-back .brand { left: 50%; top: 92px; transform: translateX(-50%); }
  .card-back .brand-dot { background: var(--paper); }
  .social-row {
    position: absolute; left: 50%; bottom: 62px; transform: translateX(-50%);
    display: flex; align-items: center; gap: 14px; color: var(--paper); font-size: 11px; white-space: nowrap;
  }
  .social-rule { width: 70px; height: 1px; background: rgba(255,255,255,.85); }
  .social-item { display: flex; align-items: center; gap: 5px; }
  .social-square { width: 12px; height: 12px; border-radius: 2px; background: var(--paper); }
</style>
</head>
<body>
  <section class="card card-front">
    <svg class="card-art" viewBox="0 0 540 309" aria-hidden="true">
      <defs>
        <linearGradient id="bandBlue" x1="0" y1="0" x2="0" y2="1">
          <stop offset="0" stop-color="#34a7d8"/>
          <stop offset="1" stop-color="#0455a3"/>
        </linearGradient>
        <linearGradient id="arcShade" x1="0" y1="0" x2="1" y2="0">
          <stop offset="0" stop-color="#000" stop-opacity=".9"/>
          <stop offset="1" stop-color="#000" stop-opacity="0"/>
        </linearGradient>
      </defs>
      <rect width="540" height="309" fill="url(#bandBlue)"/>
      <path d="M360 0 C470 30 510 160 482 309 H460 C488 160 455 40 350 0 Z" fill="url(#arcShade)"/>
      <path d="M0 0 H350 C455 40 488 160 460 309 H0 Z" fill="#fff"/>
    </svg>
    <div class="front-website">www.harlowcreek.org</div>
    <div class="brand">
      <span class="brand-dot"></span>
      <span class="brand-name"><span class="line-main">HARLOW CREEK</span><span class="line-sub">CHURCH</span></span>
    </div>
    <div class="contact">
      <p>2847 Tamsin Parkway<br>Ashgrove Valley 27594</p>
      <p class="contact-phone">
        <span class="phone-icon">
          <svg width="11" height="11" viewBox="0 0 24 24" aria-hidden="true"><path fill="#fff" d="M6.6 10.8a15.1 15.1 0 0 0 6.6 6.6l2.2-2.2c.3-.3.7-.4 1-.2 1.1.4 2.3.6 3.6.6.6 0 1 .4 1 1V20c0 .6-.4 1-1 1A17 17 0 0 1 3 4c0-.6.4-1 1-1h3.5c.6 0 1 .4 1 1 0 1.3.2 2.5.6 3.6.1.3 0 .7-.2 1z"/></svg>
        </span>
        (919) 482-7093
      </p>
      <p class="service-label">SERVICE TIMES:</p>
      <p class="service-times">Sunday @ 8:30 AM and 11:00 AM</p>
    </div>
  </section>

  <section class="card card-back">
    <div class="brand">
      <span class="brand-dot"></span>
      <span class="brand-name"><span class="line-main">HARLOW CREEK</span><span class="line-sub">CHURCH</span></span>
    </div>
    <div class="social-row">
      <span class="social-rule"></span>
      <span class="social-item"><span class="social-square"></span>Chatterly</span>
      <span class="social-item"><span class="social-square"></span>Snapwell</span>
      <span class="social-item"><span class="social-square"></span>ClipHarbor</span>
      <span class="social-rule"></span>
    </div>
  </section>
</body>
</html>
```